Wine Label Design-Hollow Creek Vineyard

Hollow Creek Vineyard is in the Barossa Valley in South Australia. The Barossa is recognized as Australia's premier wine region, producing Australia's icon wines and some " new takes on traditional".
This family owned and operated vineyard grows some exceptionally high quality fruit. Most of the fruit is sold and used for some of Australia's most iconic wines. Small quantities are retained by the owners for some wines with very limited availability. (Wines were previously sold as Brackwell Vineyards Hollow Creek ( Shiraz, Cabernet etc).

The wines will in the future be labeled simply ‘Hollow Creek Vineyard’. The label will launch this new identity for the single family single vineyard and its high quality wines which are a true expression of the vineyard and derive from the Hollow Creek common to this ancient area (800-2000 million years old).
The label should reflect
• Single vineyard, family owned
• vines in very old rock & soils
• High quality & reliability
• Edgy but true, design based thinking (Please note:blue is generally seen as an unacceptable colour for a wine label?? Don’t ask me why)

The wines will be sold mostly direct in Australia ( ie not through retail stores), with limited export to Asia, Scandinavia and Canada.
There are three quality levels and price points in the portfolio
1. Entry level premium for everyday drinking for discriminating drinkers-approx AUD20
2. Super Premium-approx AUD30
3. Limited Release ultlra premium-AUD75-90?
We envisage three variations on the label but with an obvious & common design element. This design element should be able to be used for corporate identification and promotion
The paper stock will be waterproof and self adhesive. Our preference is for designs that engage the user by appealing to both sight and touch. It is preferred that textures be added eg embossing, high build varnish etc-rather than be a facet of the stock itself.
For information on statutory label requirements refer to www.vintnerregistry-example.com . In brief
o Front label need not show any mandatory information. However we would prefer Variety, Barossa Valley, Year and alcohol to be shown on the front label
o Back label should show all mandatories and allow for a bar code
Updates

Project Deadline Extended
Reason: I've had a problem with my wireless broadband account and reception has been intermittent to say the least to the extent that I switched off at the weekend. Just going downtown now for a 'polite discussion' with my service provider.

Project Deadline Extended
Reason: I have receiver insufficient designs of quality which we would consider. Too many designs have a "cut and paste" appearance - too few exhibit an original art/design element which truly identifies the product.

Gals & Guys

most of the designs submitted lack punch and originality and are totally unmemorable.
Please-get on Searcho or whatever enter "Wine Label Designs" and do some research b4 u waste your time and mine. Formulaic cut and paste will not win the day. That's not to say that cut and paste can't work-but it must have some originality, impact and command attention. Please surprise me.

Following on from a question from a designer about who is our competition and what we are looking for I sent the following 
"I don't think I can add anything new. Read the brief and comments again and research wine labels on the web. In 30 minutes you'll get a good idea of the creative edgy designs in the industry. There are a plethora of collections. Our competition-anyone with a label. In 2010 there were over 2400 "producers" in other words 2400 producers with at least one label. In fact there are over 25000 Australian wines and then the numerous imported wines.

Target Market(s)

$20 people who budget everyday but have graduated from drinking 'entry level' wines. These people will likely fit into Cat. (b) in the $30 wine

$30 (a) will not over-compromise on some everyday discretionary expenditure.(b) might buy for special occasions

$70-$90 Professional/successful people with high disposable/discretionary income not particularly worried about recession. wine geeks.

Industry/Entity Type

Retail

Requirements
Must have
• identifiable element across range of wines

```html
<!DOCTYPE html>
<html lang="en">
<head>
<meta charset="utf-8">
<title>Hollow Creek Vineyard – Front Label</title>
<link rel="stylesheet" href="https://fonts.googleapis.com/css2?family=Tinos&display=swap">
<style>
  :root {
    --backdrop: #e4e4e4;
    --band-grey: #9b9b9b;
    --band-black: #0d0d0d;
    --label-red: #b9504e;
    --frame-black: #111111;
    --rock-light: #d2d2d2;
    --rock-mid: #a4a4a4;
    --rock-dark: #5e5e5e;
    --ink: #111111;
  }
  * { box-sizing: border-box; margin: 0; padding: 0; }
  html, body {
    width: 1200px;
    height: 1200px;
    overflow: hidden;
    background: var(--backdrop);
  }
  .canvas {
    position: relative;
    width: 1200px;
    height: 1200px;
  }
  .label {
    position: absolute;
    left: 240px;
    top: 140px;
    width: 720px;
    height: 920px;
    background: var(--label-red);
    overflow: hidden;
  }
  .label__band-top {
    position: absolute;
    left: 0; top: 0;
    width: 100%; height: 200px;
    background: var(--band-grey);
  }
  .label__band-black {
    position: absolute;
    left: 0; top: 200px;
    width: 100%; height: 52px;
    background: var(--band-black);
  }
  .label__rule-bottom {
    position: absolute;
    left: 0; top: 813px;
    width: 100%; height: 24px;
    background: var(--band-black);
  }
  .label__band-bottom {
    position: absolute;
    left: 0; top: 837px;
    width: 100%; height: 83px;
    background: var(--band-grey);
  }
  .label__frame {
    position: absolute;
    left: 120px;
    top: 13px;
    width: 472px;
    height: 568px;
    background: var(--frame-black);
    padding: 16px;
  }
  .label__rock {
    position: relative;
    width: 100%;
    height: 100%;
    background: linear-gradient(160deg, var(--rock-dark) 0%, var(--rock-light) 35%, var(--rock-mid) 70%, var(--rock-dark) 100%);
  }
  .label__name {
    position: absolute;
    left: 0; right: 0;
    top: 130px;
    text-align: center;
    font-family: "Tinos", "Times New Roman", serif;
    font-weight: 400;
    font-size: 62px;
    line-height: 100px;
    color: var(--ink);
  }
  .label__vintage,
  .label__region {
    position: absolute;
    left: 0; right: 0;
    text-align: center;
    font-family: "Tinos", "Times New Roman", serif;
    font-weight: 400;
    color: var(--ink);
  }
  .label__vintage { top: 648px; font-size: 58px; }
  .label__region { top: 742px; font-size: 52px; }
  .label__alcohol {
    position: absolute;
    right: 12px;
    bottom: 8px;
    font-family: "Tinos", "Times New Roman", serif;
    font-size: 14px;
    color: var(--ink);
  }
</style>
</head>
<body>
  <main class="canvas">
    <section class="label" aria-label="Hollow Creek Vineyard front label">
      <div class="label__band-top"></div>
      <div class="label__band-black"></div>
      <div class="label__frame">
        <div class="label__rock" role="img" aria-label="Black and white photograph of weathered rock outcrop under a cloudy sky"></div>
        <h1 class="label__name">Hollow Creek<br>Vineyard</h1>
      </div>
      <p class="label__vintage">2012</p>
      <p class="label__region">Barossa Valley</p>
      <div class="label__rule-bottom"></div>
      <div class="label__band-bottom"></div>
      <p class="label__alcohol">13.5% Alc/Vol</p>
    </section>
  </main>
</body>
</html>
```